Website to design and sell sundials: www.gnomonvale.com

We have a website that creates a free paper sundial, we want to migrate from this not profit free website to a website where we will continue offering the free paper sundial model but We will also offer a manufactured sundial and sell it.
In order to understand the project, please visit:
http://www.gnomonvale.com/vertical/sundial.html and
http://www.torvel.net/landing/

The website user journey should be redesigned, including the phases that are,
select language
Show product give info
Creation/edit sundial (could be one or more phases)
View created sundial
Buy sundial.

May some of them could be combined or splitted, what It have more sense.

Requirements
Must have
• A description page user journey offering freemium paper sundial and physical sundial to sell.
• A sundial creation page for "free" paper sundial
• A result page for paper sundial
• A sell page for physical

```html
<!DOCTYPE html>
<html lang="en">
<head>
<meta charset="utf-8">
<title>GnomonVale – Edit Sundial</title>
<link href="https://fonts.googleapis.com/css2?family=Open+Sans:wght@400;600&family=Titillium+Web:wght@400;600&display=swap" rel="stylesheet">
<style>
:root{
  --red:#b5120b;
  --red-dark:#9c0e08;
  --orange:#e8a23a;
  --nav:#1f1f1f;
  --nav-lang:#333333;
  --ink:#333333;
  --muted:#666666;
  --line:#d6d6d6;
  --grey-bg:#ececea;
  --white:#ffffff;
  --map:#e7e3da;
}
*{box-sizing:border-box;margin:0;padding:0}
html,body{width:846px;height:1200px;overflow:hidden;background:var(--white)}
body{position:relative;font-family:"Open Sans",sans-serif;color:var(--ink)}
.abs{position:absolute}
.heading{font-family:"Titillium Web",sans-serif;font-weight:400}

/* header */
.brand{left:78px;top:34px;display:flex;align-items:center;gap:8px;font-family:"Titillium Web",sans-serif;font-weight:600;font-size:24px;color:var(--red)}
.brand-mark{width:12px;height:12px;background:var(--red);border-radius:50%}
.search{left:532px;top:25px;width:235px;height:33px;border:1px solid #cfcfcf;border-radius:2px;font-size:8px;color:#999;padding:11px 10px}
.search svg{position:absolute;right:10px;top:12px}

/* nav */
.nav{left:0;top:82px;width:846px;height:40px;background:var(--nav)}
.nav-item{top:0;height:40px;line-height:40px;font-size:8px;font-weight:600;color:var(--white);text-transform:uppercase}
.nav-item.active{background:var(--orange);width:81px;text-align:center}
.nav-lang{left:694px;width:73px;background:var(--nav-lang);text-align:center}
.flag{display:inline-block;width:16px;height:10px;background:#dfe3ee;vertical-align:middle;margin-right:4px}

/* location */
.band{left:0;top:122px;width:846px;height:329px;background:var(--red)}
.map-frame{left:78px;top:140px;width:690px;height:342px;background:var(--white);box-shadow:0 16px 14px -10px rgba(0,0,0,.35)}
.map{left:5px;top:5px;width:680px;height:331px;background:linear-gradient(135deg,#ece8df 0%,#e2ded4 45%,#f0d9a8 60%,#d9dde3 85%,#a9c2d8 100%)}
.map-overlay{left:5px;top:189px;width:680px;height:142px;background:rgba(185,22,14,.88)}
.map-title{left:28px;top:20px;font-size:20px;line-height:24px;color:var(--white);letter-spacing:.3px}
.map-text{left:28px;top:46px;width:630px;font-size:8px;color:var(--white);line-height:18px;white-space:nowrap}
.map-input{left:28px;top:93px;width:511px;height:37px;background:var(--white);border-radius:2px}
.go{left:551px;top:93px;width:66px;height:37px;background:#151515;color:var(--white);font-family:"Titillium Web",sans-serif;font-weight:600;font-size:12px;text-align:center;line-height:37px;border-radius:2px}

/* fields */
.label{font-size:9px;color:var(--muted)}
.field{height:25px;border:1px solid #cfcfcf;border-radius:2px;background:var(--white);font-size:7px;color:#999;padding:8px 7px}
.select{font-size:7px;color:#555;padding:9px 9px}
.select::after{content:"";position:absolute;right:9px;top:11px;border:3px solid transparent;border-top:4px solid #444}

/* options */
.options{left:0;top:630px;width:846px;height:336px;background:var(--grey-bg)}
.opt-title{left:97px;top:30px;font-size:19px;line-height:24px;color:var(--ink)}
.opt-title span{color:var(--red)}
.photo{width:111px;height:74px;border:2px solid var(--white);box-shadow:0 0 2px rgba(0,0,0,.3)}
.radio{width:12px;height:12px;border:1px solid #cfcfcf;border-radius:50%;background:var(--white)}
.radio.on::after{content:"";position:absolute;left:3px;top:3px;width:5px;height:5px;border-radius:50%;background:#555}
.check{width:12px;height:12px;border:1px solid #cfcfcf;background:var(--white)}
.check svg{position:absolute;left:2px;top:2px}
.create{left:352px;top:296px;width:143px;height:40px;background:var(--orange);color:#2a2a2a;font-family:"Titillium Web",sans-serif;font-weight:600;font-size:12px;line-height:40px;text-align:center}
.rule{left:72px;top:965px;width:689px;height:2px;background:#c99235}

/* footer */
.col-title{font-size:12.5px;line-height:16px;color:var(--ink)}
.foot-text{font-size:7.5px;color:var(--muted);line-height:21.5px}
.divider{top:998px;width:1px;height:128px;background:#e2e2e2}
.link{font-size:7.5px;color:var(--muted)}
.more{font-size:9px;color:var(--red)}
.bottom{left:0;top:1140px;width:846px;height:60px;background:var(--red)}
.copy{left:78px;top:22px;font-size:8.5px;color:var(--white)}
.social{top:22px;width:14px;height:14px}
</style>
</head>
<body>

<header>
  <div class="abs brand"><span class="brand-mark"></span>GnomonVale.com</div>
  <div class="abs search">Search...
    <svg width="9" height="9" viewBox="0 0 10 10"><circle cx="4" cy="4" r="3" fill="none" stroke="#888" stroke-width="1.3"/><line x1="6.3" y1="6.3" x2="9" y2="9" stroke="#888" stroke-width="1.3"/></svg>
  </div>
</header>

<nav class="abs nav">
  <div class="abs nav-item" style="left:93px">Home</div>
  <div class="abs nav-item" style="left:154px">Products</div>
  <div class="abs nav-item active" style="left:217px">Edit Sundial</div>
  <div class="abs nav-item" style="left:322px">About Us</div>
  <div class="abs nav-item" style="left:398px">News</div>
  <div class="abs nav-item" style="left:456px">Contact Us</div>
  <div class="abs nav-item nav-lang"><span class="flag"></span>EN ▾</div>
</nav>

<section class="location">
  <div class="abs band"></div>
  <div class="abs map-frame">
    <div class="abs map" role="img" aria-label="Street map of the city centre for choosing the sundial location"></div>
    <div class="abs map-overlay">
      <h1 class="abs map-title heading">SUNDIAL LOCATION</h1>
      <p class="abs map-text">Select the location where you want to place your paper sundial, mark a line along building wall where you want to put it. Write your address and press Go!<br>(e.g. Picadilly circus, london, UK)</p>
      <div class="abs map-input"></div>
      <div class="abs go">GO</div>
    </div>
  </div>

  <div class="abs label" style="left:98px;top:525px">Longitude :</div>
  <div class="abs field" style="left:154px;top:518px;width:68px">0</div>
  <div class="abs label" style="left:254px;top:525px">Latitude :</div>
  <div class="abs field" style="left:302px;top:518px;width:68px">0</div>
  <div class="abs label" style="left:411px;top:525px">Wall declination :</div>
  <div class="abs field" style="left:495px;top:518px;width:69px">0</div>

  <div class="abs label" style="left:98px;top:576px">Now select the face of the building</div>
  <div class="abs field select" style="left:256px;top:571px;width:62px;height:26px">A</div>
</section>

<section class="abs options">
  <h2 class="abs opt-title heading"><span>SUNDIAL</span> OPTIONS</h2>

  <div class="abs photo" style="left:98px;top:76px;background:linear-gradient(90deg,#4a5a66 0%,#a85a43 35%,#b86b4f 100%)" role="img" aria-label="Paper sundial fixed on a brick wall"></div>
  <div class="abs radio on" style="left:221px;top:105px"></div>
  <div class="abs label" style="left:239px;top:105px">Wall sundial</div>

  <div class="abs photo" style="left:316px;top:76px;background:linear-gradient(90deg,#1c1c1c 0%,#2b2b2b 30%,#b9a88f 55%,#8aa0b6 100%)" role="img" aria-label="Paper sundial placed on a window"></div>
  <div class="abs radio" style="left:438px;top:105px"></div>
  <div class="abs label" style="left:456px;top:105px">Window sundial</div>

  <div class="abs label" style="left:98px;top:181px">Banner :</div>
  <div class="abs field" style="left:153px;top:175px;width:117px">Paper sundial</div>
  <div class="abs label" style="left:286px;top:181px">Timezone :</div>
  <div class="abs field select" style="left:345px;top:175px;width:167px">(GMT +999) LOCAL TIME (SOLAR TIME)</div>

  <div class="abs label" style="left:97px;top:221px">Solar Time :</div>
  <div class="abs radio" style="left:154px;top:222px"></div>
  <div class="abs label" style="left:182px;top:221px">Civil Time :</div>
  <div class="abs radio on" style="left:233px;top:222px"></div>

  <div class="abs label" style="left:97px;top:256px">Daylight Saving Time :</div>
  <div class="abs check" style="left:195px;top:257px"><svg width="8" height="8" viewBox="0 0 8 8"><path d="M1 4 L3 6 L7 1.5" fill="none" stroke="#555" stroke-width="1.2"/></svg></div>
  <div class="abs label" style="left:236px;top:256px">Equation of time :</div>
  <div class="abs check" style="left:321px;top:257px"><svg width="8" height="8" viewBox="0 0 8 8"><path d="M1 4 L3 6 L7 1.5" fill="none" stroke="#555" stroke-width="1.2"/></svg></div>

  <div class="abs create">CREATE SUNDIAL
    <svg width="10" height="10" viewBox="0 0 10 10" style="vertical-align:-1px;margin-left:3px"><circle cx="5" cy="5" r="5" fill="#2a2a2a"/><path d="M4 3 L7 5 L4 7Z" fill="var(--orange)"/></svg>
  </div>
</section>
<div class="abs rule"></div>

<footer>
  <h3 class="abs col-title heading" style="left:78px;top:1003px">CREATED SUNDIAL</h3>
  <p class="abs foot-text" style="left:78px;top:1022px;width:272px">This page is about Sundials. Sundials are instruments that tell you the time with the shadow of the sun. To design a sundial you need to know exactly where you are going to put it.</p>
  <div class="abs more" style="left:78px;top:1095px">
    <svg width="8" height="8" viewBox="0 0 10 10" style="vertical-align:-1px"><circle cx="5" cy="5" r="5" fill="var(--red)"/><path d="M4 3 L7 5 L4 7Z" fill="#fff"/></svg> CLICK MORE DETAILS
  </div>

  <div class="abs divider" style="left:382px"></div>
  <h3 class="abs col-title heading" style="left:433px;top:1003px">QUICK LINKS</h3>
  <div class="abs link" style="left:433px;top:1029px">Privacy Policy</div>
  <div class="abs link" style="left:433px;top:1051px">Site Security</div>
  <div class="abs link" style="left:433px;top:1072px">Terms of Use</div>
  <div class="abs link" style="left:433px;top:1094px">Site Map</div>

  <div class="abs divider" style="left:576px"></div>
  <h3 class="abs col-title heading" style="left:608px;top:1003px">CONTACT</h3>
  <svg class="abs" style="left:611px;top:1029px" width="7" height="10" viewBox="0 0 7 10"><path d="M3.5 0 A3.5 3.5 0 0 1 7 3.5 C7 6 3.5 10 3.5 10 C3.5 10 0 6 0 3.5 A3.5 3.5 0 0 1 3.5 0Z" fill="var(--red)"/><circle cx="3.5" cy="3.5" r="1.3" fill="#fff"/></svg>
  <div class="abs link" style="left:625px;top:1029px;color:#444;font-size:8px">SUNDIAL</div>
  <div class="abs link" style="left:625px;top:1042px;line-height:14.5px">123, Lorem Ipsm, Lorem Ipsm<br>Lorem Ipsm - 123 456</div>
  <svg class="abs" style="left:609px;top:1079px" width="11" height="8" viewBox="0 0 11 8"><rect width="11" height="8" rx="1" fill="var(--red)"/><path d="M0.5 0.8 L5.5 4.5 L10.5 0.8" fill="none" stroke="#fff" stroke-width="0.9"/></svg>
  <div class="abs link" style="left:627px;top:1080px;color:#444;font-size:8px">0123 456 78900</div>
  <svg class="abs" style="left:609px;top:1106px" width="10" height="10" viewBox="0 0 10 10"><rect width="10" height="10" rx="2" fill="var(--red)"/><path d="M3 2.3 L4.3 4 L3.6 4.8 Q4.5 6 5.4 6.5 L6.2 5.8 L7.8 7.2 L7 8 Q4 7.6 2.2 3.2Z" fill="#fff"/></svg>
  <div class="abs link" style="left:628px;top:1106px;color:#444;font-size:8px">info@gnomonvale.com</div>

  <div class="abs bottom">
    <div class="abs copy">Copyright ©2016 Sundial. All Rights reserved.</div>
    <div class="abs social" style="left:696px;background:#3b5b9a"></div>
    <div class="abs social" style="left:715px;background:#3aa4e0"></div>
    <div class="abs social" style="left:733px;background:#1c7ab4"></div>
    <div class="abs social" style="left:752px;background:#d8503f"></div>
  </div>
</footer>

</body>
</html>
```